Investment company needing business card

We are wanting a business card which looks sharp and easy on the eye. We are thinking of having a business card with the logo embossed on it, to really make it stand out. We will only have a small amount of information of the business card, person's name, position, email address and phone number

Contact Information for Business Card

Danielle Frost
Executive Assistant
+64 21 473 5162
danielf@harwickpartners.co.nz

Requirements
Must have
• Embossed logo
Should not have
• Not to be busy

```html
<!DOCTYPE html>
<html lang="en">
<head>
<meta charset="utf-8">
<title>Harwick Partners – Business Card</title>
<link href="https://fonts.googleapis.com/css2?family=Arimo:wght@400;700&display=swap" rel="stylesheet">
<style>
  :root {
    --backdrop: #141517;
    --card-light: #e5e5e5;
    --brand-green: #21a66a;
    --rule-grey: #5b5c5e;
    --mark-grey: #58595b;
    --card-dark: #0e0e0e;
    --emboss: #050505;
    --on-green: #ffffff;
  }
  html, body {
    margin: 0;
    width: 1200px;
    height: 965px;
    overflow: hidden;
    background: var(--backdrop);
    font-family: "Arimo", Arial, sans-serif;
  }
  .card {
    position: absolute;
    left: 277px;
    width: 648px;
    height: 369px;
    overflow: hidden;
  }
  .card--front { top: 97px; background: var(--card-light); }
  .card--back { top: 504px; background: var(--card-dark); }

  .brand {
    position: absolute;
    display: flex;
    align-items: center;
    gap: 16px;
  }
  .card--front .brand { left: 35px; top: 49px; }
  .card--back .brand { left: 128px; top: 145px; }
  .brand__square {
    width: 80px;
    height: 80px;
    background: var(--mark-grey);
  }
  .brand__name {
    font-weight: 700;
    font-size: 38px;
    letter-spacing: 0.5px;
    color: var(--brand-green);
  }
  .card--back .brand__square { background: var(--emboss); }
  .card--back .brand__name { color: var(--emboss); }

  .rule {
    position: absolute;
    left: 0;
    width: 100%;
    height: 5px;
    background: var(--rule-grey);
  }
  .rule--top { top: 186px; }
  .rule--bottom { top: 335px; }

  .band {
    position: absolute;
    left: 0;
    top: 193px;
    width: 100%;
    height: 140px;
    background: var(--brand-green);
    color: var(--on-green);
  }
  .person__name {
    position: absolute;
    left: 34px;
    top: 20px;
    margin: 0;
    font-size: 20px;
    font-weight: 400;
  }
  .person__role {
    position: absolute;
    left: 34px;
    top: 46px;
    margin: 0;
    font-size: 15px;
  }
  .contact {
    position: absolute;
    left: 34px;
    top: 91px;
    margin: 0;
    padding: 0;
    list-style: none;
    font-size: 15px;
    line-height: 19px;
  }
  .contact li { display: flex; align-items: center; gap: 6px; }
  .contact svg { width: 12px; height: 12px; }
</style>
</head>
<body>
  <section class="card card--front">
    <div class="brand">
      <div class="brand__square"></div>
      <div class="brand__name">HARWICK PARTNERS</div>
    </div>
    <div class="rule rule--top"></div>
    <div class="band">
      <h1 class="person__name">DANIELLE FROST</h1>
      <p class="person__role">Executive Assistant</p>
      <ul class="contact">
        <li>
          <svg viewBox="0 0 12 12" aria-hidden="true">
            <circle cx="6" cy="6" r="6" fill="#e5e5e5"/>
            <path d="M3.6 3.2l1.2-.3.6 1.4-.7.6a4 4 0 0 0 1.6 1.6l.6-.7 1.4.6-.3 1.2c-2.6.2-4.6-1.8-4.4-4.4z" fill="#21a66a"/>
          </svg>
          +64 21 473 5162
        </li>
        <li>
          <svg viewBox="0 0 12 12" aria-hidden="true">
            <circle cx="6" cy="6" r="6" fill="#e5e5e5"/>
            <rect x="3" y="4" width="6" height="4.2" fill="none" stroke="#21a66a" stroke-width="0.9"/>
            <path d="M3 4l3 2.3L9 4" fill="none" stroke="#21a66a" stroke-width="0.9"/>
          </svg>
          danielf@harwickpartners.co.nz
        </li>
      </ul>
    </div>
    <div class="rule rule--bottom"></div>
  </section>

  <section class="card card--back">
    <div class="brand">
      <div class="brand__square"></div>
      <div class="brand__name">HARWICK PARTNERS</div>
    </div>
  </section>
</body>
</html>
```